Business Card Design

We are a manufacturing and distribution company with most of our customer base being supermarkets. We have established brand guidelines that are attached.

```html
<!DOCTYPE html>
<html lang="en">
<head>
<meta charset="utf-8">
<title>Corvale Business Card</title>
<link href="https://fonts.googleapis.com/css2?family=Montserrat:wght@500;700;800&family=Arimo:wght@400&display=swap" rel="stylesheet">
<style>
  :root {
    --stage: #2b2b2c;
    --card-dark: #231f20;
    --brand-red: #e21b23;
    --brand-blue: #0a6ab4;
    --paper: #ffffff;
    --ink: #111111;
  }
  * { margin: 0; padding: 0; box-sizing: border-box; }
  html, body { width: 1200px; height: 1015px; overflow: hidden; }
  body {
    background: var(--stage);
    position: relative;
    font-family: "Arimo", Arial, sans-serif;
  }
  .card {
    position: absolute;
    width: 580px;
    height: 331px;
    border-radius: 4px;
    overflow: hidden;
    box-shadow: 0 18px 40px rgba(0,0,0,.55);
  }
  .card--back { left: 70px; top: 110px; background: var(--card-dark); }
  .card--front { left: 550px; top: 560px; background: var(--paper); }

  .brand {
    display: flex;
    align-items: center;
    gap: 16px;
    font-family: "Montserrat", Arial, sans-serif;
    font-weight: 800;
    color: var(--paper);
    letter-spacing: 3px;
    white-space: nowrap;
  }
  .brand__mark { width: 26px; height: 26px; background: var(--brand-red); flex: none; }
  .card--back .brand { position: absolute; left: 0; right: 0; top: 136px; justify-content: center; font-size: 44px; }

  .front__top {
    position: absolute; left: 0; top: 0; width: 100%; height: 150px;
    background: var(--card-dark);
  }
  .card--front .brand { position: absolute; left: 120px; top: 52px; font-size: 46px; }
  .front__info {
    position: absolute; left: 0; top: 150px; width: 100%; height: 96px;
    background: var(--brand-red);
    display: flex; align-items: center;
    color: var(--paper);
  }
  .person {
    flex: none; width: 290px; text-align: right; padding-right: 20px;
    white-space: nowrap;
  }
  .person__name {
    font-family: "Montserrat", Arial, sans-serif; font-weight: 800;
    font-size: 23px; letter-spacing: 1px; line-height: 1.1;
  }
  .person__role { font-size: 17px; letter-spacing: .5px; margin-top: 2px; }
  .divider { flex: none; width: 1.5px; height: 64px; background: var(--paper); }
  .contacts {
    list-style: none; padding-left: 20px; font-size: 16px; letter-spacing: .3px;
    white-space: nowrap;
  }
  .contacts li { display: flex; align-items: center; gap: 10px; line-height: 22px; }
  .contacts svg { width: 16px; height: 16px; flex: none; }
  .front__address {
    position: absolute; left: 0; top: 246px; width: 100%; height: 66px;
    display: flex; align-items: center; justify-content: center;
    font-size: 19px; color: var(--ink); letter-spacing: .5px; white-space: nowrap;
  }
  .front__stripe {
    position: absolute; left: 0; bottom: 0; width: 100%; height: 19px;
    display: flex;
  }
  .front__stripe span { flex: 1; }
  .stripe--red { background: var(--brand-red); }
  .stripe--blue { background: var(--brand-blue); }
</style>
</head>
<body>

  <section class="card card--back" aria-label="Business card, back">
    <div class="brand"><span class="brand__mark"></span>CORVALE</div>
  </section>

  <section class="card card--front" aria-label="Business card, front">
    <div class="front__top">
      <div class="brand"><span class="brand__mark"></span>CORVALE</div>
    </div>

    <div class="front__info">
      <div class="person">
        <p class="person__name">DANIEL HARWOOD</p>
        <p class="person__role">Managing Director</p>
      </div>
      <div class="divider"></div>
      <ul class="contacts">
        <li>
          <svg viewBox="0 0 24 24" fill="none" stroke="currentColor" stroke-width="2.4" stroke-linecap="round"><path d="M5 3h4l2 5-3 2a12 12 0 0 0 6 6l2-3 5 2v4a2 2 0 0 1-2 2A18 18 0 0 1 3 5a2 2 0 0 1 2-2z"/></svg>
          044-555 010 247
        </li>
        <li>
          <svg viewBox="0 0 24 24" fill="none" stroke="currentColor" stroke-width="2.2"><rect x="2" y="5" width="20" height="14"/><path d="M2 5l10 8 10-8"/></svg>
          info@corvale-foods.com
        </li>
        <li>
          <svg viewBox="0 0 24 24" fill="none" stroke="currentColor" stroke-width="2"><circle cx="12" cy="12" r="10"/><path d="M2 12h20M12 2c3 3 3 17 0 20M12 2c-3 3-3 17 0 20"/></svg>
          www.corvale-foods.com
        </li>
      </ul>
    </div>

    <p class="front__address">27 Harbour Lane, Westfield 30418, Northland</p>

    <div class="front__stripe">
      <span class="stripe--red"></span>
      <span class="stripe--blue"></span>
    </div>
  </section>

</body>
</html>
```